Logo, Web and Mobile Designs for enterprise social media platform

All the details are in the attached document, please start reading the scope document first which explains what is this project about and the details about the needed deliverables, after that please read the UI_Requirements document which will detail what is expected regarding the coded web version since this is a coded contest, it is very important that you meet the UI requirements or suggest something else but we will need to agree first before working on the coded version

Good Luck

Target Market(s)

Enterprise Social Media

Industry/Entity Type

Media

Coding

Coded - Design and coding required

Number of Pages Required

5+ page

Font styles to use
Sans Serif

Requirements
Must have
• All the must haves are listed in the scope document so please check before you start

```html
<!DOCTYPE html>
<html lang="en">
<head>
<meta charset="utf-8">
<title>Teamora – Security Details</title>
<link href="https://fonts.googleapis.com/css2?family=Roboto:wght@300;400;500&display=swap" rel="stylesheet">
<style>
:root{
  --blue:#1a8bc6;
  --blue-dark:#1279b0;
  --footer:#1f8bb8;
  --orange:#f6a01a;
  --text:#555a60;
  --muted:#777;
  --line:#dedede;
  --bg:#ebebeb;
  --side:#f3f3f3;
  --white:#fff;
}
*{box-sizing:border-box;margin:0;padding:0}
html,body{width:1200px;height:826px;overflow:hidden;background:var(--bg)}
body{font-family:'Roboto',sans-serif;color:var(--text)}
.page{width:1400px;height:964px;position:relative;transform:scale(0.857143);transform-origin:0 0;background:var(--bg)}
.abs{position:absolute}

/* header */
.topbar{left:0;top:0;width:1400px;height:82px;background:var(--white);border-bottom:1px solid var(--line)}
.menu-btn{left:118px;top:34px;width:20px}
.menu-btn span{display:block;height:3px;background:#7a7f85;margin-bottom:4px;border-radius:1px}
.vdiv{top:0;width:1px;height:82px;background:#ececec}
.brand{left:196px;top:18px;display:flex;align-items:center;gap:10px}
.brand-mark{width:50px;height:46px;border-radius:50%;background:var(--orange)}
.brand-name{font-size:37px;font-weight:500;color:var(--blue);letter-spacing:.5px}
.avatar{left:870px;top:23px;width:40px;height:40px;border-radius:50%;background:linear-gradient(135deg,#5a5a5a,#b8a89a)}
.user-name{left:925px;top:31px;font-size:19px;color:#555}
.caret{left:1036px;top:39px}
.icon{position:absolute}
.badge{position:absolute;width:24px;height:18px;border-radius:9px;color:#fff;font-size:13px;text-align:center;line-height:18px;font-weight:500}

/* card */
.card{left:115px;top:123px;width:1168px;height:623px;background:var(--white);border:1px solid #d8d8d8}
.sidebar{left:0;top:0;width:325px;height:621px;background:var(--side);border-right:2px solid #e3e3e3}
.side-main{position:absolute;left:0;width:323px;display:flex;align-items:center;gap:16px;padding-left:20px;font-size:18px;color:#444;border-bottom:2px solid #e6e6e6}
.side-list{position:absolute;left:0;top:150px;width:323px;list-style:none}
.side-list li{height:38px;display:flex;align-items:center;padding-left:20px;gap:20px;font-size:19px;font-weight:300;color:#444;border-bottom:1px solid #e3e3e3}
.side-list li.active{color:var(--blue);font-weight:400}

/* panel */
.panel{left:362px;top:47px;width:770px;height:445px;border:1px solid #e6e6e6;background:var(--white)}
.panel-head{height:57px;background:#f5f6f8;border-bottom:1px solid #e3e3e3;display:flex;align-items:center;padding-left:24px;gap:12px;font-size:18px;color:#444}
.label{font-size:16.5px;color:#555}
.switch-label{font-size:13px;color:#555}
.toggle{width:56px;height:28px;border:1px solid #ddd;border-radius:14px;background:#f7f7f7}
.toggle::before{content:"";position:absolute;left:4px;top:4px;width:19px;height:19px;border-radius:50%;background:#666}
.btn{background:var(--blue);color:#fff;font-size:18px;font-weight:500;text-align:center;border-bottom:3px solid var(--blue-dark);border-radius:2px;letter-spacing:.3px}
.field{width:527px;height:46px;border:1px solid #ddd;font-size:13px;padding-left:21px;line-height:44px;color:#444}

/* footer */
.footer{left:0;top:792px;width:1400px;height:172px;background:var(--footer);color:#fff;text-align:center}
.social{position:absolute;top:33px;left:598px;display:flex;gap:16px}
.social span{width:28px;height:28px;background:#fff;border-radius:5px}
.foot-nav{position:absolute;top:83px;width:100%;font-size:16.5px;font-weight:300}
.foot-nav span{margin:0 8px}
.copy{position:absolute;top:117px;width:100%;font-size:16.5px}
</style>
</head>
<body>
<div class="page">
  <header class="topbar abs">
    <div class="menu-btn abs"><span></span><span></span><span></span></div>
    <div class="vdiv abs" style="left:168px"></div>
    <div class="brand abs"><div class="brand-mark"></div><div class="brand-name">Teamora</div></div>
    <div class="avatar abs" role="img" aria-label="User profile photo"></div>
    <div class="user-name abs">Corwin Ashby</div>
    <svg class="caret abs" width="13" height="8" viewBox="0 0 13 8"><path d="M0 0h13L6.5 8z" fill="#555"/></svg>
    <div class="vdiv abs" style="left:1076px"></div>
    <svg class="icon" style="left:1103px;top:31px" width="24" height="22" viewBox="0 0 24 22">
      <rect x="0" y="0" width="24" height="5" fill="#555"/><rect x="0" y="8" width="24" height="5" fill="#555"/><rect x="0" y="16" width="12" height="5" fill="#555"/><rect x="14" y="16" width="10" height="5" fill="#aaa"/>
    </svg>
    <div class="badge" style="left:1116px;top:19px;background:var(--orange)">8</div>
    <div class="vdiv abs" style="left:1156px"></div>
    <svg class="icon" style="left:1180px;top:30px" width="24" height="24" viewBox="0 0 24 24"><circle cx="10" cy="10" r="7.5" fill="none" stroke="#555" stroke-width="3"/><path d="M15.5 15.5L22 22" stroke="#555" stroke-width="3.5" stroke-linecap="round"/></svg>
    <div class="vdiv abs" style="left:1226px"></div>
    <svg class="icon" style="left:1251px;top:31px" width="22" height="24" viewBox="0 0 22 24"><path d="M11 1c-5 0-7 4-7 8v6l-3 4h20l-3-4V9c0-4-2-8-7-8z" fill="#555"/><circle cx="11" cy="21.5" r="2.5" fill="#555"/></svg>
    <div class="badge" style="left:1259px;top:19px;background:var(--blue)">8</div>
  </header>

  <main class="card abs">
    <nav class="sidebar abs">
      <div class="side-main" style="top:0;height:68px">
        <svg width="18" height="16" viewBox="0 0 18 16"><rect width="8" height="7" rx="1" fill="#1a8bc6"/><rect x="10" width="8" height="7" rx="1" fill="#1a8bc6"/><rect y="9" width="8" height="7" rx="1" fill="#1a8bc6"/><rect x="10" y="9" width="8" height="7" rx="1" fill="#1a8bc6"/></svg>
        <span>VIEW DASHBOARD</span>
      </div>
      <div class="side-main" style="top:68px;height:62px">
        <svg width="18" height="18" viewBox="0 0 18 18"><rect x="1" y="3" width="16" height="14" rx="1" fill="none" stroke="#1a8bc6" stroke-width="2"/><rect x="1" y="3" width="16" height="4" fill="#1a8bc6"/><path d="M5 1v4M13 1v4" stroke="#1a8bc6" stroke-width="2"/><path d="M4 10h10M4 13h10M7 8v8M11 8v8" stroke="#1a8bc6" stroke-width="1"/></svg>
        <span>VIEW EVENT</span>
      </div>
      <ul class="side-list">
        <li><span>›</span>About Us</li>
        <li><span>›</span>Speakers</li>
        <li><span>›</span>Track</li>
        <li><span>›</span>Sessions</li>
        <li><span>›</span>Tickets</li>
        <li><span>›</span>Organizers</li>
        <li><span>›</span>Sponsors</li>
        <li><span>›</span>Exhibitor</li>
        <li class="active"><span style="color:#444">›</span>SECURITY</li>
        <li><span>›</span>Members</li>
      </ul>
    </nav>

    <section class="panel abs">
      <div class="panel-head">
        <svg width="12" height="16" viewBox="0 0 12 16"><path d="M3 7V4a3 3 0 0 1 6 0" fill="none" stroke="#555" stroke-width="2"/><rect x="0" y="7" width="12" height="9" rx="1" fill="#555"/></svg>
        <span>SECURITY DETAILS</span>
      </div>
      <div class="label abs" style="left:26px;top:111px">Event Type :</div>
      <div class="switch-label abs" style="left:216px;top:115px">PRIVATE</div>
      <div class="toggle abs" style="left:277px;top:108px"></div>
      <div class="btn abs" style="left:216px;top:153px;width:110px;height:37px;line-height:36px">SAVE</div>
      <div class="label abs" style="left:26px;top:227px">Members :</div>
      <div class="field abs" style="left:216px;top:213px">User Search</div>
      <div class="label abs" style="left:26px;top:287px">Administrators :</div>
      <div class="field abs" style="left:216px;top:273px">User Search</div>
      <div class="btn abs" style="left:216px;top:346px;width:212px;height:42px;line-height:41px">SEND INVITATION</div>
    </section>
  </main>

  <footer class="footer abs">
    <div class="social" aria-label="Social links"><span></span><span></span><span></span><span></span><span></span></div>
    <div class="foot-nav">Home <span>/</span> Contact <span>/</span> Topics <span>/</span> Posts and Comments <span>/</span> Discussion <span>/</span> Videos Links</div>
    <div class="copy">Copyright @ 2015 - 2015.Teamora. All Rights Reserved.</div>
  </footer>
</div>
</body>
</html>
```